Chamber of Commerce Web Brightform Project

We are working with Harborlight Chamber of Commerce. They are a new chamber of commerce forming in SoCal.
Some sites to use for inspiration:
https://brevinmarchamber.org
https://quellford.org
https://www.dorwickhavenchamber.com
https://www.tpchamber.com
https://velmorintcc.org
Thank you for taking the time to consider designing a website for us. We are web developers based in Stockton, CA, USA. Most of our projects go through the same process. Understanding this process may help you win a project with us. We custom-code all of our websites in-house. We don’t have any requirements as to what tools you use for your Brightform, but we prefer Figma files. For any Brightform that we label as four-stars, we send it to the client for review. The client picks the final Brightform they want us to use. Once we complete this process, we will continue to show additional clients all the four-star sites and purchase them later. Your designs will have multiple chances to sell. For better chances of success, we ask that you follow these guidelines.
IMAGES:
If you use any images or icons in the Brightform, we ask that you have a link to the asset so we can purchase the image/icon. Most of the designs we submit do not have the customer’s images on them unless they have some great images. Be creative; show us the feeling you are trying to portray with your image choices. Use any royalty-free site you choose. We subscribe to Adobe and mainly use their images, but we can purchase images outside of Adobe.
PLEASE NOTE: we will not submit designs to clients with watermarks on the images.
FONTS:
We ask that you identify the fonts used in the Brightform. This can be done in a message if you want. We typically use Google Fonts and Adobe Fonts.
CONTENT:
We're always open to different content and ideas. We often submit designs with stock images so the client can see our vision. We typically take pictures after the website launch to use their images with our vision. Lorem Ipsum is fine for paragraphs, but we ask that you write the headers in correct English. We want to be able to show the vision and identify the sections of the website.
INSPIRATION:
We typically add a couple of links in the brief of websites we like to help you get started in your Brightform.
REVISIONS:
We do not often ask for revisions of the designs unless we see something in the Brightform that may not appeal to the client. If there are slight changes that we want to make, we do that in the development process.
FEEDBACK:
We rarely give feedback on designs during the Brightform process. We are working on many website projects and do not have the time to provide feedback. We usually respond if your request is well thought out and asks specific questions, but a note asking “feedback, please” usually goes unanswered.

```html
<!DOCTYPE html>
<html lang="en">
<head>
<meta charset="utf-8">
<title>Harborlight Chamber of Commerce</title>
<link href="https://fonts.googleapis.com/css2?family=Bebas+Neue&family=Montserrat:wght@400;500;600;700&display=swap" rel="stylesheet">
<style>
:root{
  --navy:#1a3a8f;
  --blue:#2457c5;
  --deep:#0f2a6e;
  --yellow:#f7c21b;
  --orange:#f3a12a;
  --ink:#1b1b1b;
  --muted:#555;
  --line:#d9d9d9;
  --dark:#1d1d1d;
  --pale:#e3eaf7;
  --white:#fff;
}
*{box-sizing:border-box;margin:0;padding:0}
html,body{width:1200px;height:4474px;overflow:hidden}
body{position:relative;background:var(--white);font-family:"Montserrat",sans-serif;color:var(--ink)}
.abs{position:absolute}
.heading{font-family:"Bebas Neue",sans-serif;font-size:46px;letter-spacing:1px;color:var(--ink);display:flex;align-items:center;justify-content:center;gap:18px;position:absolute;left:0;width:1200px}
.dot-mark{width:28px;height:28px;border-radius:50%;background:var(--blue);display:inline-block}
.btn{position:absolute;display:flex;align-items:center;justify-content:center;border-radius:30px;background:var(--navy);color:#fff;font-weight:700;font-size:14px;box-shadow:0 0 0 3px #fff,0 0 0 5px var(--navy)}
/* header */
.brand{position:absolute;left:110px;top:22px;display:flex;align-items:center;gap:12px}
.brand-name{font-family:"Bebas Neue",sans-serif;font-size:56px;line-height:.9;color:var(--blue)}
.brand-sub{font-family:"Bebas Neue",sans-serif;font-size:25px;color:var(--blue);letter-spacing:.5px}
.callbar{position:absolute;left:634px;top:0;width:330px;height:40px;background:var(--navy);border-radius:0 0 0 22px;color:#fff;display:flex;align-items:center;gap:10px;padding-left:38px;font-size:13px}
.callbar b{font-weight:700;font-size:15px}
.phone-ic{width:30px;height:30px;border-radius:50%;border:2px solid #fff;display:flex;align-items:center;justify-content:center}
.join{position:absolute;left:960px;top:0;width:240px;height:40px;background:var(--yellow);font-weight:700;font-size:15px;padding-left:40px;display:flex;align-items:center}
.nav{position:absolute;top:80px;left:596px;display:flex;gap:38px;font-size:13px;font-weight:500}
.nav .active{color:var(--blue);border-bottom:2px solid var(--blue)}
/* hero */
.hero-title{position:absolute;top:235px;left:0;width:1200px;text-align:center;font-family:"Bebas Neue",sans-serif;font-size:54px;line-height:54px;color:#fff;letter-spacing:1px}
.hero-title span{color:var(--yellow)}
.hero-text{position:absolute;top:364px;left:0;width:1200px;text-align:center;color:#fff;font-size:17px;line-height:30px}
.hero-btn{position:absolute;left:520px;top:454px;width:154px;height:38px;border-radius:20px;background:var(--yellow);font-weight:700;font-size:14px;display:flex;align-items:center;justify-content:center;box-shadow:0 0 0 4px var(--navy),0 0 0 6px var(--yellow)}
/* about */
.about-title{position:absolute;left:633px;top:830px;font-family:"Bebas Neue",sans-serif;font-size:46px;display:flex;gap:12px;align-items:center}
.about-text{position:absolute;left:630px;top:896px;width:390px;font-size:13.5px;line-height:27.5px;color:#333}
/* clients */
.client{position:absolute;top:1398px;height:99px;background:#fff;box-shadow:0 2px 10px rgba(0,0,0,.15);display:flex;align-items:center;justify-content:center;gap:8px;font-size:23px;font-weight:600;color:var(--ink);white-space:nowrap}
.client i{width:18px;height:18px;background:var(--ink);display:block;flex:none}
.dots{position:absolute;top:1549px;left:573px;display:flex;gap:14px}
.dots span{width:12px;height:12px;border-radius:50%;background:#bbb}
.dots .on{background:var(--navy);box-shadow:0 0 0 3px #ccd}
/* services */
.svc-band{position:absolute;left:0;top:1646px;width:1200px;height:326px;background:linear-gradient(90deg,#f29f25,#f4ab38 50%,#f29f25)}
.svc-card{position:absolute;top:1840px;width:313px;height:223px;background:#fff;box-shadow:0 3px 12px rgba(0,0,0,.15);text-align:center}
.svc-ic{position:absolute;left:106px;top:-50px;width:100px;height:100px;border-radius:50%;background:var(--navy);box-shadow:0 0 0 3px #fff,0 0 0 5px var(--orange);display:flex;align-items:center;justify-content:center}
.svc-card h3{margin-top:78px;font-size:18px;font-weight:600}
.svc-card p{margin:14px auto 0;width:250px;font-size:13px;line-height:27px;color:#444}
.arrow{position:absolute;top:1921px;width:38px;height:38px;border-radius:50%;background:#fff;border:2px solid var(--ink);display:flex;align-items:center;justify-content:center}
/* events */
.ev-card{position:absolute;top:2234px;width:311px;height:344px;background:#fff;border:1px solid var(--line);box-shadow:0 2px 8px rgba(0,0,0,.08)}
.ev-img{height:188px;width:100%}
.ev-date{position:absolute;right:16px;top:154px;width:70px;height:70px;border-radius:50%;background:var(--navy);color:#fff;text-align:center;font-weight:700;font-size:22px;line-height:24px;padding-top:12px;border:4px solid #fff}
.ev-date small{display:block;font-size:13px}
.ev-card h4{position:absolute;left:21px;top:218px;font-size:18px;font-weight:600}
.ev-card p{position:absolute;left:21px;top:252px;width:260px;font-size:13px;line-height:26px;color:#555}
.ev-time{position:absolute;left:21px;top:310px;font-size:13px;font-weight:600;display:flex;gap:6px;align-items:center}
/* blogs */
.blog-band{position:absolute;left:0;top:2745px;width:1200px;height:737px;background:linear-gradient(180deg,#dfe7f6,#e8eef9)}
.blog-card{position:absolute;background:#fff;box-shadow:0 2px 10px rgba(0,0,0,.1)}
.blog-card .img{width:100%}
.blog-card h4{font-size:17px;font-weight:600;line-height:26px;margin:12px 14px 0}
.blog-date{display:flex;gap:8px;align-items:center;color:var(--navy);font-weight:600;font-size:13px;margin:8px 14px 0}
.blog-card p{font-size:13px;line-height:26px;color:#444;margin:6px 14px 0}
.read{color:var(--navy);font-weight:700;font-size:13px;margin:2px 14px 0}
/* contact */
.field{position:absolute;border:1.5px solid #555;border-radius:24px;font-size:12px;padding-left:22px;display:flex;align-items:center;color:#333}
/* footer */
.f-head{position:absolute;top:4152px;color:#fff;font-size:18px;font-weight:500}
.f-list{position:absolute;top:4190px;list-style:none;color:#fff;font-size:14px}
.f-list li{height:34.5px;display:flex;gap:10px;align-items:center}
.f-contact{position:absolute;left:873px;color:#fff;font-size:14px;line-height:26px;display:flex;gap:14px;align-items:center}
.f-ic{width:32px;height:32px;border-radius:50%;background:#fff;display:flex;align-items:center;justify-content:center;flex:none}
</style>
</head>
<body>

<!-- Header -->
<div class="brand">
  <span class="dot-mark" style="width:46px;height:46px"></span>
  <div><div class="brand-name">HARBORLIGHT</div><div class="brand-sub">CHAMBER OF COMMERCE</div></div>
</div>
<div class="callbar">CALL US <span class="phone-ic"><svg width="14" height="14" viewBox="0 0 24 24"><path fill="#fff" d="M6.6 10.8a15 15 0 006.6 6.6l2.2-2.2c.3-.3.7-.4 1-.2 1.1.4 2.3.6 3.6.6.6 0 1 .4 1 1V20c0 .6-.4 1-1 1A17 17 0 013 4c0-.6.4-1 1-1h3.5c.6 0 1 .4 1 1 0 1.3.2 2.5.6 3.6.1.3 0 .7-.2 1z"/></svg></span><b>+1 800 555 0142</b></div>
<div class="join">JOIN US</div>
<nav class="nav"><span class="active">HOME</span><span>ABOUT US</span><span>EVENTS</span><span>BLOGS</span><span>CONTACT US</span></nav>

<!-- Hero -->
<svg class="abs" style="left:0;top:127px" width="1200" height="590" viewBox="0 127 1200 590">
  <defs><linearGradient id="heroGrad" x1="0" y1="0" x2="0" y2="1"><stop offset="0" stop-color="#3a6fd6"/><stop offset=".55" stop-color="#1e4fb8"/><stop offset="1" stop-color="#123c9a"/></linearGradient></defs>
  <path role="img" aria-label="Photo of a business crowd in silhouette against a city skyline" fill="url(#heroGrad)" d="M0 127H1200V685H180Q25 680 0 470Z"/>
  <path fill="none" stroke="var(--yellow)" stroke-width="8" d="M0 485Q25 693 185 697H1200"/>
  <path fill="none" stroke="var(--blue)" stroke-width="6" d="M0 505Q28 705 190 707H1200"/>
</svg>
<h1 class="hero-title">FUELING LOCAL <span>GROWTH,</span><br>BUILDING STRONGER <span>COMMUNITIES.</span></h1>
<p class="hero-text">Lorem Ipsum is simply dummy text of the printing<br>and typesetting industry.</p>
<div class="hero-btn">GET STARTED</div>

<!-- About -->
<div class="abs" role="img" aria-label="Chamber emblem artwork" style="left:150px;top:805px;width:400px;height:400px;border-radius:50%;background:radial-gradient(circle at 50% 40%,#e7b84a,#3a6fd6 65%,#1a3a8f)"></div>
<h2 class="about-title">ABOUT US <span class="dot-mark"></span></h2>
<p class="about-text">Lorem Ipsum is simply dummy text of the printing and typesetting industry. Lorem Ipsum has been the industry's standard dummy text ever since the 1500s, when an unknown printer took a galley of type and scrambled it to make a type specimen book.<br>It has survived not only five centuries, but also the leap into electronic typesetting, remaining essentially unchanged.</p>
<div class="btn" style="left:628px;top:1148px;width:154px;height:38px">READ MORE</div>

<!-- Clients -->
<h2 class="heading" style="top:1305px"><span class="dot-mark"></span>OUR CLIENTS<span class="dot-mark"></span></h2>
<div class="client" style="left:115px;width:183px"><i></i>Brightform</div>
<div class="client" style="left:315px;width:182px">Tellwick</div>
<div class="client" style="left:512px;width:182px">Norvane</div>
<div class="client" style="left:710px;width:183px">Quillstead</div>
<div class="client" style="left:905px;width:183px">Delmaro</div>
<div class="dots"><span class="on"></span><span></span><span></span></div>

<!-- Services -->
<div class="svc-band"></div>
<h2 class="heading" style="top:1704px"><span class="dot-mark" style="background:#fff"></span>OUR SERVICES<span class="dot-mark" style="background:#fff"></span></h2>
<div class="svc-card" style="left:111px"><div class="svc-ic"><svg width="50" height="50" viewBox="0 0 24 24" fill="none" stroke="#fff" stroke-width="1.3"><circle cx="12" cy="12" r="9"/><path d="M3 12h18M12 3c3 3 3 15 0 18M12 3c-3 3-3 15 0 18"/></svg></div><h3>Networking Opportunities</h3><p>Lorem Ipsum is simply dummy text of the printing and typesetting industry.</p></div>
<div class="svc-card" style="left:444px"><div class="svc-ic"><svg width="50" height="50" viewBox="0 0 24 24" fill="none" stroke="#fff" stroke-width="1.3"><rect x="7" y="3" width="10" height="7"/><circle cx="6" cy="15" r="2"/><circle cx="12" cy="15" r="2"/><circle cx="18" cy="15" r="2"/><path d="M3 21c0-2 6-2 6 0M9 21c0-2 6-2 6 0M15 21c0-2 6-2 6 0"/></svg></div><h3>Advocacy &amp; Representation</h3><p>Lorem Ipsum is simply dummy text of the printing and typesetting industry.</p></div>
<div class="svc-card" style="left:775px"><div class="svc-ic"><svg width="50" height="50" viewBox="0 0 24 24" fill="none" stroke="#fff" stroke-width="1.3"><circle cx="12" cy="10" r="8"/><circle cx="12" cy="8" r="2"/><path d="M8 14c1-3 7-3 8 0M4 19l5-2 3 2 3-2 5 2"/></svg></div><h3>Member Business Directory</h3><p>Lorem Ipsum is simply dummy text of the printing and typesetting industry.</p></div>
<div class="arrow" style="left:32px"><svg width="16" height="16" viewBox="0 0 24 24"><path d="M15 4l-8 8 8 8" fill="none" stroke="#000" stroke-width="3"/></svg></div>
<div class="arrow" style="left:1124px;border-color:var(--navy)"><svg width="16" height="16" viewBox="0 0 24 24"><path d="M9 4l8 8-8 8" fill="none" stroke="var(--navy)" stroke-width="3"/></svg></div>

<!-- Events -->
<h2 class="heading" style="top:2140px"><span class="dot-mark"></span>OUR EVENTS<span class="dot-mark"></span></h2>
<div class="abs" style="left:98px;top:2250px;width:311px;height:338px;background:var(--yellow)"></div>
<div class="ev-card" style="left:108px"><div class="ev-img" role="img" aria-label="Photo of stacked hands in teamwork" style="background:linear-gradient(135deg,#3d4a56,#b98a6a 55%,#2d3b48)"></div><div class="ev-date">10<small>Feb</small></div><h4>Lorem Ipsum</h4><p>Feb 10 - simply dummy text of the printing and typesetting industry.</p><div class="ev-time"><svg width="15" height="15" viewBox="0 0 24 24" fill="none" stroke="#000" stroke-width="2"><circle cx="12" cy="12" r="9"/><path d="M12 7v5l3 2"/></svg>8.00 AM - 1:00 PM</div></div>
<div class="ev-card" style="left:445px"><div class="ev-img" role="img" aria-label="Photo of a digital globe over a circuit board" style="background:radial-gradient(circle at 50% 45%,#3c8ad0,#0c2544 70%)"></div><div class="ev-date">16<small>Feb</small></div><h4>Lorem Ipsum</h4><p>Feb 16 - simply dummy text of the printing and typesetting industry.</p><div class="ev-time"><svg width="15" height="15" viewBox="0 0 24 24" fill="none" stroke="#000" stroke-width="2"><circle cx="12" cy="12" r="9"/><path d="M12 7v5l3 2"/></svg>8.00 AM - 1:00 PM</div></div>
<div class="ev-card" style="left:779px"><div class="ev-img" role="img" aria-label="Photo of a waterfront city skyline at sunset" style="background:linear-gradient(180deg,#7c6f8a,#e08a4a 55%,#3b3140)"></div><div class="ev-date">19<small>Feb</small></div><h4>Lorem Ipsum</h4><p>Feb 19 - simply dummy text of the printing and typesetting industry.</p><div class="ev-time"><svg width="15" height="15" viewBox="0 0 24 24" fill="none" stroke="#000" stroke-width="2"><circle cx="12" cy="12" r="9"/><path d="M12 7v5l3 2"/></svg>8.00 AM - 1:00 PM</div></div>
<div class="btn" style="left:522px;top:2639px;width:154px;height:38px">VIEW MORE</div>

<!-- Blogs -->
<div class="blog-band"></div>
<h2 class="heading" style="top:2823px"><span class="dot-mark"></span>OUR BLOGS<span class="dot-mark"></span></h2>
<div class="blog-card" style="left:102px;top:2903px;width:476px;height:382px">
  <div class="img" role="img" aria-label="Photo of colleagues meeting around a laptop" style="height:250px;background:linear-gradient(135deg,#8a8f96,#c9c5bd 50%,#4a4540)"></div>
  <h4 style="font-size:22px;line-height:31px;margin:18px 18px 0">Lorem Ipsum is simply dummy text of the printing and typesetting</h4>
  <div class="blog-date" style="margin:10px 18px 0"><svg width="18" height="18" viewBox="0 0 24 24" fill="none" stroke="var(--navy)" stroke-width="2"><rect x="3" y="5" width="18" height="16" rx="2"/><path d="M3 10h18M8 3v4M16 3v4"/></svg>March 30,2023</div>
</div>
<div class="blog-card" style="left:594px;top:2903px;width:241px;height:382px">
  <div class="img" role="img" aria-label="Photo of a smiling business team" style="height:195px;background:linear-gradient(135deg,#6f8a6a,#c8a98a 50%,#5a5a60)"></div>
  <h4>Lorem Ipsum is simply dummy text printing</h4>
  <div class="blog-date"><svg width="15" height="15" viewBox="0 0 24 24" fill="none" stroke="var(--navy)" stroke-width="2"><rect x="3" y="5" width="18" height="16" rx="2"/><path d="M3 10h18M8 3v4M16 3v4"/></svg>March 30,2023</div>
  <p>Lorem Ipsum is simply dummy text of the printing</p><div class="read">READ MORE</div>
</div>
<div class="blog-card" style="left:850px;top:2903px;width:242px;height:382px">
  <div class="img" role="img" aria-label="Photo of a harbor skyline at dusk" style="height:195px;background:linear-gradient(180deg,#5a7bc0,#e4904d 55%,#2f3a55)"></div>
  <h4>Lorem Ipsum is simply dummy text printing</h4>
  <div class="blog-date"><svg width="15" height="15" viewBox="0 0 24 24" fill="none" stroke="var(--navy)" stroke-width="2"><rect x="3" y="5" width="18" height="16" rx="2"/><path d="M3 10h18M8 3v4M16 3v4"/></svg>March 30,2023</div>
  <p>Lorem Ipsum is simply dummy text of the printing</p><div class="read">READ MORE</div>
</div>
<div class="btn" style="left:520px;top:3344px;width:154px;height:38px">VIEW MORE</div>

<!-- Contact -->
<h2 class="heading" style="top:3554px"><span class="dot-mark"></span>CONTACT US<span class="dot-mark"></span></h2>
<div class="field" style="left:208px;top:3632px;width:377px;height:47px">NAME</div>
<div class="field" style="left:601px;top:3632px;width:379px;height:47px">E MAIL</div>
<div class="field" style="left:208px;top:3698px;width:377px;height:47px">PHONE</div>
<div class="field" style="left:601px;top:3698px;width:379px;height:47px">SUBJECT</div>
<div class="field" style="left:208px;top:3763px;width:770px;height:115px;align-items:flex-start;padding-top:16px;border-radius:20px">MESSAGE</div>
<div class="btn" style="left:510px;top:3919px;width:172px;height:40px">SEND MESSAGE</div>

<!-- Footer -->
<svg class="abs" style="left:0;top:4030px" width="1200" height="444" viewBox="0 4030 1200 444">
  <path fill="var(--dark)" d="M0 4062H1030Q1190 4066 1200 4210V4474H0Z"/>
  <path fill="none" stroke="var(--blue)" stroke-width="6" d="M0 4040H1035Q1195 4045 1205 4180"/>
  <path fill="none" stroke="var(--yellow)" stroke-width="8" d="M0 4051H1032Q1192 4056 1202 4195"/>
</svg>
<div class="brand" style="top:4168px">
  <span class="dot-mark" style="width:38px;height:38px"></span>
  <div><div class="brand-name" style="font-size:44px">HARBORLIGHT</div><div class="brand-sub" style="font-size:19px">CHAMBER OF COMMERCE</div></div>
</div>
<div class="f-head" style="left:428px">QUICK LINKS</div>
<ul class="f-list" style="left:428px"><li>➜ Home</li><li>➜ About Us</li><li>➜ Events</li><li>➜ Blogs</li><li>➜ Contact Us</li></ul>
<div class="f-head" style="left:660px">HELP LINKS</div>
<ul class="f-list" style="left:660px;top:4186px"><li>➜ Our Blog</li><li>➜ FAQ</li><li>➜ Terms of use</li><li>➜ Privacy Policy</li><li>➜ Support Links</li></ul>
<div class="f-head" style="left:873px">CONTACT US</div>
<div class="f-contact" style="top:4195px"><span class="f-ic"><svg width="14" height="14" viewBox="0 0 24 24"><path fill="#1d1d1d" d="M12 2a7 7 0 017 7c0 5-7 13-7 13S5 14 5 9a7 7 0 017-7zm0 4a3 3 0 100 6 3 3 0 000-6z"/></svg></span><span>Harborlight Chamber,<br>2140 Lantern Bay Drive</span></div>
<div class="f-contact" style="top:4260px"><span class="f-ic"><svg width="14" height="14" viewBox="0 0 24 24"><path fill="#1d1d1d" d="M6.6 10.8a15 15 0 006.6 6.6l2.2-2.2c.3-.3.7-.4 1-.2 1.1.4 2.3.6 3.6.6.6 0 1 .4 1 1V20c0 .6-.4 1-1 1A17 17 0 013 4c0-.6.4-1 1-1h3.5c.6 0 1 .4 1 1 0 1.3.2 2.5.6 3.6.1.3 0 .7-.2 1z"/></svg></span><span>+1 800 555 0142</span></div>
<div class="f-contact" style="top:4312px"><span class="f-ic"><svg width="14" height="14" viewBox="0 0 24 24"><path fill="#1d1d1d" d="M3 5h18v14H3zm2 2v.5l7 5 7-5V7l-7 5z"/></svg></span><span>info@harborlight.org</span></div>
<div class="abs" style="left:108px;top:4400px;width:978px;height:1px;background:#666"></div>
<p class="abs" style="top:4428px;left:0;width:1200px;text-align:center;color:#fff;font-size:13px">Copyrights@2025. Harborlight Chamber of Commerce .All Rights Reserved</p>

</body>
</html>
```